Reach Crafters Unique Marketing Website Design

I am starting a new company that is a thought leader in the marketing consulting space. The company is called Reach Crafters. We intend to build a Wordpress site on the Astra Theme with the Spectra builder. Our goal is to become the leading voice that empowers high-ticket service business leaders to become Reach Crafters by equipping them with the cutting-edge frameworks and decision grade intelligence taught in leading business schools. What we are looking for is a website design that is clean and professional, making some use of white space well also being eye catching and distinctive in the consulting space. We will probably want to have a video on the homepage not in the hero section, but just below to explain the company and what we do. Our tagline is "Be found. Be chosen." I have attached a brand guide with some messaging, our typography choices, and our color system. The full site will have a primary nav that is four pages - About us, Services, Insights (essentially a blog), and Contact Us. The goal of this project is to develop an art direction that I can give to a designer to build loads of new pages.

Target Market(s)

Business owners (mostly male) from 30-60 years old, looking to fix their sales and marketing funnel.

Industry/Entity Type

Marketing consulting

Font styles to use
Sans Serif

Requirements
Must have
• A clean, professional design that builds trust with owners of high-ticket service businesses. We need a space for explainer video, and sections that tell prospects what we do. Would also like to have a blog carousel.
Nice to have
• Social feeds, if possible. See attached documents for colors and fonts.
Should not have
• Our feel is professional enough to be trustworthy, but unique enough to be memorable. Cartoon ideas do not meet the professional test, and we do not want the website to appear feminine.

```html
<!DOCTYPE html>
<html lang="en">
<head>
<meta charset="utf-8">
<title>Reach Crafters — Be Found. Be Chosen.</title>
<link rel="stylesheet" href="https://fonts.googleapis.com/css2?family=Oswald:wght@300;400;500;600&family=Inter:ital,wght@0,400;0,500;0,600;0,700;1,400;1,500&display=swap">
<style>
:root{
  --blue:#2f55f4;
  --blue-dark:#2446d8;
  --navy:#0b1630;
  --navy-2:#0f1c36;
  --ink:#1b1f2a;
  --text:#545a66;
  --muted:#8a8f99;
  --light:#f5f6f8;
  --white:#ffffff;
  --star:#f08a24;
  --head:'Oswald',sans-serif;
  --body:'Inter',sans-serif;
}
*{margin:0;padding:0;box-sizing:border-box}
html,body{width:1200px;height:4850px;overflow:hidden}
body{font-family:var(--body);color:var(--ink);background:var(--white);position:relative}
.section{position:absolute;left:0;width:1200px}
.wrap{position:relative;width:918px;margin:0 auto;height:100%}
.h-title{font-family:var(--head);font-weight:500;font-size:37px;text-align:center;color:var(--ink);letter-spacing:.2px}
.h-title em{font-style:normal;color:var(--blue)}
.rule{width:46px;height:2px;background:var(--blue);margin:16px auto 0}
.lede{font-size:14px;color:var(--text);text-align:center;line-height:1.6}
.btn{display:inline-flex;align-items:center;gap:8px;background:var(--blue);color:var(--white);font-size:13px;font-weight:500;padding:0 20px;height:40px;text-decoration:none}
.arrow{width:16px;height:8px}

/* header */
.site-header{top:0;height:78px;background:var(--white);border-bottom:1px solid #eceef2}
.brand{position:absolute;left:70px;top:12px}
.brand-name{font-family:var(--body);font-weight:700;font-size:26px;color:var(--ink);letter-spacing:.5px}
.brand-tag{font-size:11px;font-style:italic;color:var(--text);margin:4px 0 0 66px}
.nav{position:absolute;right:70px;top:20px;display:flex;align-items:center;gap:0}
.nav a{font-size:12.5px;color:var(--text);text-decoration:none;margin-left:52px}
.nav .btn{height:36px;font-size:12.5px;padding:0 16px;margin-left:52px;color:var(--white)}

/* hero */
.hero{top:78px;height:544px;background:linear-gradient(90deg,#141a22 0%,#1c2530 40%,#3c4b55 62%,#2c6a6a 80%,#3e4e5a 100%)}
.hero-photo{position:absolute;inset:0;background:linear-gradient(90deg,rgba(10,14,20,.9) 0%,rgba(10,14,20,.55) 45%,rgba(10,14,20,0) 75%)}
.hero-copy{position:absolute;left:72px;top:122px;width:420px;color:var(--white)}
.hero-kicker{font-size:17px;font-style:italic;font-weight:500}
.hero-title{font-family:var(--head);font-size:40px;line-height:1.2;margin-top:18px}
.hero-title strong{font-weight:600;display:block}
.hero-title strong span{border-bottom:4px solid var(--blue)}
.hero-title .thin{font-weight:300;display:block}
.hero-text{font-size:13.5px;line-height:1.65;margin-top:14px;color:#e5e8ee}
.hero .btn{margin-top:28px;height:40px}

/* features */
.features{top:622px;height:554px;background:var(--light)}
.features .h-title{padding-top:62px}
.features .lede{margin-top:22px}
.feature-row{display:flex;justify-content:space-between;margin-top:34px}
.feature{width:283px;height:284px;background:var(--white);padding:28px 28px;box-shadow:0 2px 10px rgba(0,0,0,.04)}
.feature svg{width:62px;height:62px}
.feature h3{font-size:16px;font-weight:600;margin-top:22px}
.feature .bar{width:36px;height:1px;background:#d0d4dc;margin:14px 0}
.feature p{font-size:11.5px;line-height:1.7;color:var(--text)}

/* video */
.video{top:1176px;height:814px;background:var(--white)}
.video .h-title{padding-top:62px}
.video .lede{margin:22px auto 0;width:640px}
.video-frame{position:absolute;left:0;top:216px;width:918px;height:518px;background:var(--white);padding:8px;box-shadow:0 4px 16px rgba(0,0,0,.12)}
.video-still{width:100%;height:100%;background:linear-gradient(135deg,#3a3530 0%,#6e5d50 35%,#4b4640 65%,#2c2a28 100%);position:relative}
.play{position:absolute;left:50%;top:50%;width:62px;height:62px;margin:-31px 0 0 -31px}

/* stats */
.stats{top:1990px;height:398px;background:linear-gradient(120deg,var(--navy) 0%,#0f1e3d 55%,#0b1630 100%)}
.stat-row{position:absolute;left:150px;top:78px;display:flex;gap:42px}
.stat{width:194px;text-align:center;color:var(--white)}
.stat svg{width:194px;height:194px}
.stat-label{font-size:14px;margin-top:20px}

/* about */
.about{top:2388px;height:562px;background:var(--white)}
.about-photo{position:absolute;left:0;top:76px;width:417px;height:410px;background:linear-gradient(90deg,#dfe7ef 0%,#c9d3dd 50%,#eef1f4 52%,#d9dde2 100%)}
.about-copy{position:absolute;left:483px;top:118px;width:435px}
.about-copy h2{font-family:var(--head);font-weight:500;font-size:36px}
.about-copy h2 span{font-family:var(--body);font-weight:700;font-size:31px;color:var(--blue);letter-spacing:.3px}
.about-copy h4{font-size:14.5px;font-weight:600;margin-top:22px}
.about-copy p{font-size:12px;line-height:1.72;color:var(--text);margin-top:12px}
.about-copy .btn{margin-top:24px;height:40px}

/* testimonials */
.testimonials{top:2950px;height:565px;background:var(--light)}
.testimonials .h-title{padding-top:64px}
.testimonials .lede{margin-top:22px}
.quote-row{display:flex;justify-content:space-between;margin-top:36px}
.quote{width:283px;height:256px;background:var(--white);padding:28px 26px;position:relative}
.stars{color:var(--star);font-size:14px;letter-spacing:3px}
.qmark{position:absolute;right:28px;top:22px;font-family:Georgia,serif;font-size:52px;line-height:1;color:#c7d1f7}
.quote p{font-size:11.5px;font-style:italic;line-height:1.95;color:var(--text);margin-top:14px}
.person{display:flex;align-items:center;gap:12px;position:absolute;left:26px;bottom:28px}
.avatar{width:30px;height:30px;border-radius:50%;background:var(--blue);color:var(--white);display:flex;align-items:center;justify-content:center;font-weight:700;font-size:14px}
.person b{display:block;font-size:14px;font-weight:600}
.person small{font-size:9.5px;color:var(--text)}
.dots{display:flex;justify-content:center;gap:7px;margin-top:34px}
.dots i{width:6px;height:6px;border-radius:50%;background:#cdd2dc}
.dots i:first-child{background:var(--blue)}

/* blog */
.blog{top:3515px;height:655px;background:var(--white)}
.blog .h-title{padding-top:60px}
.post-row{display:flex;justify-content:space-between;margin-top:30px}
.post{width:283px;height:360px;background:var(--white);box-shadow:0 3px 14px rgba(0,0,0,.07)}
.post-img{height:150px;position:relative}
.post-img.a{background:linear-gradient(135deg,#9b4a3a,#d9d2c4 55%,#7a5c48)}
.post-img.b{background:linear-gradient(135deg,#eef2f6,#cbd6e2 55%,#4f6d93)}
.post-img.c{background:linear-gradient(135deg,#6d7480,#b8b2a6 50%,#3e4652)}
.date{position:absolute;right:4px;top:4px;width:36px;height:42px;background:var(--blue);color:var(--white);text-align:center;line-height:1}
.date b{display:block;font-family:var(--head);font-size:21px;font-weight:500;padding-top:4px}
.date small{font-size:8px}
.post-body{padding:22px 30px}
.post h3{font-size:14.5px;font-weight:600;line-height:1.4}
.post p{font-size:11.5px;line-height:1.75;color:var(--text);margin-top:12px}
.more{display:inline-flex;align-items:center;gap:6px;color:var(--blue);font-size:12px;margin-top:8px}
.blog-cta{text-align:center;margin-top:30px}

/* cta */
.cta{top:4170px;height:325px;background:var(--blue);text-align:center;color:var(--white)}
.cta h2{font-family:var(--head);font-weight:300;font-size:40px;padding-top:80px}
.cta h2 strong{font-weight:600}
.cta p{font-size:13.5px;line-height:1.7;margin:18px auto 0;width:500px}
.cta .ghost{display:inline-flex;align-items:center;gap:8px;background:var(--white);color:var(--blue);font-size:13px;font-weight:500;height:42px;padding:0 20px;margin-top:20px}

/* footer */
.site-footer{top:4495px;height:355px;background:var(--navy-2);color:#d6dae3}
.f-col{position:absolute;top:68px}
.f-brand{left:141px;width:260px}
.f-brand .brand-name{font-size:20px;color:var(--white)}
.f-brand .tagline{font-size:10.5px;font-style:italic;margin-top:6px}
.f-brand p{font-size:12px;line-height:1.7;margin-top:20px}
.follow{display:flex;align-items:center;gap:8px;font-size:12px;margin-top:18px}
.follow i{width:22px;height:22px;border-radius:50%;border:1px solid #8793aa;display:block}
.f-col h5{font-size:15px;font-weight:600;color:var(--white)}
.f-col h5::after{content:"";display:block;width:32px;height:2px;background:var(--blue);margin-top:10px}
.f-col ul{list-style:none;margin-top:20px}
.f-col li{font-size:12px;margin-bottom:13px}
.f-links{left:449px}
.f-services{left:628px}
.f-contact{left:842px;width:230px}
.contact-item{display:flex;align-items:center;gap:14px;margin-top:20px;font-size:12px;line-height:1.7}
.contact-item .ico{flex:none;width:30px;height:30px;border-radius:50%;background:#eef1f7;display:flex;align-items:center;justify-content:center}
.contact-item .ico.blue{background:var(--blue)}
.copyright{position:absolute;left:0;right:0;bottom:14px;text-align:center;font-size:10.5px;color:#b7bdc9}
</style>
</head>
<body>

<header class="section site-header">
  <div class="brand">
    <div class="brand-name">REACH CRAFTERS</div>
    <div class="brand-tag">Be Found. Be Chosen.</div>
  </div>
  <nav class="nav">
    <a href="#">About Us</a>
    <a href="#">Services</a>
    <a href="#">Insights</a>
    <a class="btn" href="#">Contact Us</a>
  </nav>
</header>

<section class="section hero">
  <div class="hero-photo" role="img" aria-label="Photo of a team of business professionals gathered around a laptop in a modern office"></div>
  <div class="hero-copy">
    <div class="hero-kicker">Be Found. Be Chosen.</div>
    <h1 class="hero-title"><strong>Empowering <span>High-Ticket</span></strong><span class="thin">Service Business Leaders</span></h1>
    <p class="hero-text">Become a Reach Crafter with cutting-edge frameworks and decision-grade intelligence taught in leading business schools. Transform your sales and marketing funnel.</p>
    <a class="btn" href="#">Contact Us <svg class="arrow" viewBox="0 0 16 8"><path d="M0 4h14M11 1l3 3-3 3" fill="none" stroke="#fff" stroke-width="1.2"/></svg></a>
  </div>
</section>

<section class="section features">
  <div class="wrap">
    <h2 class="h-title"><em>Empowering</em> Business Leaders Like You</h2>
    <div class="rule"></div>
    <p class="lede">We provide the tools, frameworks, and intelligence you need to dominate your market.</p>
    <div class="feature-row">
      <div class="feature">
        <svg viewBox="0 0 62 62" fill="none" stroke="#2f55f4" stroke-width="1.6"><circle cx="31" cy="31" r="22"/><circle cx="31" cy="31" r="13"/><circle cx="31" cy="31" r="6"/><path d="M31 5v6M31 51v6M5 31h6M51 31h6M13 13l4 4M45 45l4 4M49 13l-4 4M17 45l-4 4"/></svg>
        <h3>Cutting-Edge Frameworks</h3>
        <div class="bar"></div>
        <p>Learn the same advanced marketing strategies taught at top business schools, tailored for high-ticket service businesses. Implement proven systems that drive consistent results.</p>
      </div>
      <div class="feature">
        <svg viewBox="0 0 62 62" fill="none" stroke="#2f55f4" stroke-width="1.6"><circle cx="31" cy="18" r="11"/><path d="M27 15a4 4 0 1 1 5 4v3M31 25v1"/><path d="M31 29v28M31 40l-12-6h-8M31 40l12-6h8M31 48l-9 4M31 48l9 4"/></svg>
        <h3>Decision-Grade Intelligence</h3>
        <div class="bar"></div>
        <p>Get data-driven insights to fix leaks in your sales and marketing funnel—fast. We turn complex data into actionable strategies that boost your bottom line.</p>
      </div>
      <div class="feature">
        <svg viewBox="0 0 62 62" fill="none" stroke="#2f55f4" stroke-width="1.6"><path d="M12 6h26l10 10v24M48 52H12V6"/><path d="M38 6v10h10M18 22h22M18 29h22M18 36h14"/><circle cx="46" cy="48" r="9"/><path d="M41 48l4 4 6-7"/></svg>
        <h3>Proven Results</h3>
        <div class="bar"></div>
        <p>Become the obvious choice for your ideal clients with positioning that commands premium fees. Join leaders who have transformed their businesses with our guidance.</p>
      </div>
    </div>
  </div>
</section>

<section class="section video">
  <div class="wrap">
    <h2 class="h-title">Discover How We <em>Transform</em> Marketing Funnels</h2>
    <div class="rule"></div>
    <p class="lede">Learn how our proven frameworks help high-ticket service businesses attract premium clients and increase conversion rates.</p>
    <div class="video-frame">
      <div class="video-still" role="img" aria-label="Explainer video still of a crowd of business people in an office">
        <svg class="play" viewBox="0 0 62 62"><circle cx="31" cy="31" r="30" fill="#fff"/><circle cx="31" cy="31" r="24" fill="#2f55f4"/><path d="M26 21l14 10-14 10z" fill="#fff"/></svg>
      </div>
    </div>
  </div>
</section>

<section class="section stats">
  <svg width="0" height="0" style="position:absolute">
    <defs>
      <pattern id="lines" width="6" height="4" patternUnits="userSpaceOnUse"><rect width="6" height="2" fill="#2f55f4"/></pattern>
    </defs>
  </svg>
  <div class="stat-row">
    <div class="stat">
      <svg viewBox="0 0 194 194"><circle cx="97" cy="97" r="96" fill="url(#lines)"/><path d="M97 1A96 96 0 0 1 97 193Z" fill="#2f55f4"/><circle cx="97" cy="97" r="68" fill="#0c1832"/><circle cx="97" cy="97" r="68" fill="none" stroke="#2f55f4" stroke-width="2"/><text x="97" y="110" text-anchor="middle" fill="#fff" font-family="Oswald,sans-serif" font-size="38" font-weight="500">170+</text></svg>
      <div class="stat-label">Clients Served</div>
    </div>
    <div class="stat">
      <svg viewBox="0 0 194 194"><circle cx="97" cy="97" r="96" fill="url(#lines)"/><path d="M97 1A96 96 0 0 1 97 193Z" fill="#2f55f4"/><circle cx="97" cy="97" r="68" fill="#0c1832"/><circle cx="97" cy="97" r="68" fill="none" stroke="#2f55f4" stroke-width="2"/><text x="97" y="110" text-anchor="middle" fill="#fff" font-family="Oswald,sans-serif" font-size="38" font-weight="500">53M+</text></svg>
      <div class="stat-label">Revenue Generated</div>
    </div>
    <div class="stat">
      <svg viewBox="0 0 194 194"><circle cx="97" cy="97" r="96" fill="url(#lines)"/><path d="M97 1A96 96 0 0 1 97 193Z" fill="#2f55f4"/><circle cx="97" cy="97" r="68" fill="#0c1832"/><circle cx="97" cy="97" r="68" fill="none" stroke="#2f55f4" stroke-width="2"/><text x="97" y="110" text-anchor="middle" fill="#fff" font-family="Oswald,sans-serif" font-size="38" font-weight="500">3.2x</text></svg>
      <div class="stat-label">Avg. ROI Increase</div>
    </div>
    <div class="stat">
      <svg viewBox="0 0 194 194"><circle cx="97" cy="97" r="96" fill="url(#lines)"/><path d="M97 1A96 96 0 0 1 97 193Z" fill="#2f55f4"/><circle cx="97" cy="97" r="68" fill="#0c1832"/><circle cx="97" cy="97" r="68" fill="none" stroke="#2f55f4" stroke-width="2"/><text x="97" y="110" text-anchor="middle" fill="#fff" font-family="Oswald,sans-serif" font-size="38" font-weight="500">92%</text></svg>
      <div class="stat-label">Client Retention</div>
    </div>
  </div>
</section>

<section class="section about">
  <div class="wrap">
    <div class="about-photo" role="img" aria-label="Photo of a consultant in a suit writing notes at a bright office desk"></div>
    <div class="about-copy">
      <h2>About <span>REACH CRAFTERS</span></h2>
      <h4>Empowering Business Leaders to Master Reach.</h4>
      <p>At Reach Crafters, we believe every high-ticket service business deserves access to the same strategic frameworks used by Top 500 companies.</p>
      <p>Our team brings together decades of experience in marketing strategy, sales optimization, and business development. We've distilled the best practices from leading business schools and real-world success stories into actionable systems that drive results.</p>
      <a class="btn" href="#">Learn More <svg class="arrow" viewBox="0 0 16 8"><path d="M0 4h14M11 1l3 3-3 3" fill="none" stroke="#fff" stroke-width="1.2"/></svg></a>
    </div>
  </div>
</section>

<section class="section testimonials">
  <div class="wrap">
    <h2 class="h-title">What Our <em>Happy Clients</em> Say About Us</h2>
    <div class="rule"></div>
    <p class="lede">We provide the tools, frameworks, and intelligence you need to dominate your market.</p>
    <div class="quote-row">
      <div class="quote">
        <div class="stars">★★★★★</div><div class="qmark">”</div>
        <p>"Reach Crafters helped us identify critical leaks in our funnel that we had overlooked for years. Our lead quality improved by 300% in just 90 days."</p>
        <div class="person"><div class="avatar">R</div><div><b>Ravi Kalmar</b><small>CEO, Northbeam Advisory</small></div></div>
      </div>
      <div class="quote">
        <div class="stars">★★★★★</div><div class="qmark">”</div>
        <p>"The frameworks provided by Reach Crafters transformed how we approach client acquisition. We've increased our average deal size by 45% while reducing acquisition costs."</p>
        <div class="person"><div class="avatar">O</div><div><b>Owen Tallis</b><small>Founder, Keystone Ventures</small></div></div>
      </div>
      <div class="quote">
        <div class="stars">★★★★★</div><div class="qmark">”</div>
        <p>"Working with Reach Crafters gave us the clarity and systems we needed to scale efficiently. Their intelligence reports alone have paid for the engagement 10x over."</p>
        <div class="person"><div class="avatar">D</div><div><b>Dana Merritt</b><small>CEO, Northbeam Advisory</small></div></div>
      </div>
    </div>
    <div class="dots"><i></i><i></i><i></i><i></i><i></i><i></i></div>
  </div>
</section>

<section class="section blog">
  <div class="wrap">
    <h2 class="h-title">Latest <em>Blog</em> Posts</h2>
    <div class="rule"></div>
    <div class="post-row">
      <article class="post">
        <div class="post-img a" role="img" aria-label="Photo of a desk with a coffee cup and a hand-drawn lead sketch"><div class="date"><b>28</b><small>JAN</small></div></div>
        <div class="post-body">
          <h3>How to 3x Your Lead Quality in 90 Days</h3>
          <p>Proven tactics from top consultants that help you attract premium clients and eliminate time-wasters...</p>
          <span class="more">Learn More <svg class="arrow" viewBox="0 0 16 8"><path d="M0 4h14M11 1l3 3-3 3" fill="none" stroke="#2f55f4" stroke-width="1.2"/></svg></span>
        </div>
      </article>
      <article class="post">
        <div class="post-img b" role="img" aria-label="Photo of a hand presenting a rising bar chart"><div class="date"><b>28</b><small>JAN</small></div></div>
        <div class="post-body">
          <h3>The Hidden Leaks Killing High-Ticket Sales</h3>
          <p>Common mistakes and fixes for service businesses struggling to convert premium prospects into...</p>
          <span class="more">Learn More <svg class="arrow" viewBox="0 0 16 8"><path d="M0 4h14M11 1l3 3-3 3" fill="none" stroke="#2f55f4" stroke-width="1.2"/></svg></span>
        </div>
      </article>
      <article class="post">
        <div class="post-img c" role="img" aria-label="Photo of two business people shaking hands in a meeting"><div class="date"><b>28</b><small>JAN</small></div></div>
        <div class="post-body">
          <h3>Positioning for Premium Clients in 2026</h3>
          <p>Be found. Be chosen. Learn the positioning strategies that make your firm the obvious choice for...</p>
          <span class="more">Learn More <svg class="arrow" viewBox="0 0 16 8"><path d="M0 4h14M11 1l3 3-3 3" fill="none" stroke="#2f55f4" stroke-width="1.2"/></svg></span>
        </div>
      </article>
    </div>
    <div class="blog-cta"><a class="btn" href="#">View All <svg class="arrow" viewBox="0 0 16 8"><path d="M0 4h14M11 1l3 3-3 3" fill="none" stroke="#fff" stroke-width="1.2"/></svg></a></div>
  </div>
</section>

<section class="section cta">
  <h2>Ready to Become a <strong>Reach Crafter?</strong></h2>
  <p>Schedule a free strategy session and discover how our frameworks can transform your sales and marketing funnel.</p>
  <a class="ghost" href="#">Schedule Your Strategy Call Now <svg class="arrow" viewBox="0 0 16 8"><path d="M0 4h14M11 1l3 3-3 3" fill="none" stroke="#2f55f4" stroke-width="1.2"/></svg></a>
</section>

<footer class="section site-footer">
  <div class="f-col f-brand">
    <div class="brand-name">REACH CRAFTERS</div>
    <div class="tagline">Be Found. Be Chosen.</div>
    <p>Lorem ipsum dolor sit amet, consectetur adipiscing elit, sed do</p>
    <div class="follow">Follow Us: <i></i><i></i><i></i></div>
  </div>
  <div class="f-col f-links">
    <h5>Quick Links</h5>
    <ul><li>About us</li><li>Services</li><li>Insights</li><li>Contact Us</li></ul>
  </div>
  <div class="f-col f-services">
    <h5>Services</h5>
    <ul><li>Executive Training</li><li>Funnel Optimization</li><li>Demand Generation</li></ul>
  </div>
  <div class="f-col f-contact">
    <h5>Contact Details</h5>
    <div class="contact-item"><span class="ico"><svg width="14" height="16" viewBox="0 0 14 16"><path d="M7 1a5 5 0 0 1 5 5c0 4-5 9-5 9S2 10 2 6a5 5 0 0 1 5-5z" fill="none" stroke="#0f1c36" stroke-width="1.4"/><circle cx="7" cy="6" r="1.8" fill="#0f1c36"/></svg></span><span>48 Harbor Lane, is simply dummy text, of the printing.</span></div>
    <div class="contact-item"><span class="ico blue"><svg width="14" height="14" viewBox="0 0 14 14"><path d="M3 1l2.5 3-1.5 1.5a8 8 0 0 0 4.5 4.5L10 8.5l3 2.5-1.5 2C6 13 1 8 1 2.5z" fill="#fff"/></svg></span><span>Phone: (555) 214 0386</span></div>
    <div class="contact-item"><span class="ico"><svg width="14" height="11" viewBox="0 0 14 11"><rect x="1" y="1" width="12" height="9" fill="none" stroke="#0f1c36" stroke-width="1.3"/><path d="M1 1l6 5 6-5" fill="none" stroke="#0f1c36" stroke-width="1.3"/></svg></span><span>hello@reachcrafters.com</span></div>
  </div>
  <div class="copyright">© 2023 Reach Crafters. All rights reserved. | Privacy Policy | Terms of Service</div>
</footer>

</body>
</html>
```